Product Label with Company Logo & Product Information

I am looking for a new label design for one of my products, Candied Pecans. I am including an old label that I made, but it does not "pop" on the current packaging. See image of current packaging attached as well.

I want the design to ultimately be something that I can take and order a roll of labels/stickers. Please stick within standard label/sticker sizes (round or square). Please include final size as well.

Must Haves:
(1) Company logo (any color variation-see attached logo images).
(2) All wording on the old label
(3) Label size can not be more than 2 in. x 4 in. (I would actually like them a little smaller). They seem kind of big as they are right now.

```html
<!DOCTYPE html>
<html lang="en">
<head>
<meta charset="utf-8">
<title>Gentle Hive – Gourmet Candied Pecans Label</title>
<link rel="stylesheet" href="https://fonts.googleapis.com/css2?family=Rye&family=Almendra:wght@400;700&family=Roboto:wght@700&display=swap">
<style>
  :root {
    --stage: #232323;
    --paper: #ffffff;
    --graphite: #58585a;
    --graphite-warm: #6f6b57;
    --honey: #ece62e;
    --ink: #4a4a4c;
  }
  html, body {
    margin: 0;
    width: 1200px;
    height: 780px;
    overflow: hidden;
    background: var(--stage);
  }
  .label {
    position: absolute;
    left: 100px;
    top: 110px;
    width: 1000px;
    height: 560px;
    background: var(--paper);
    overflow: hidden;
  }
  .label__wave {
    position: absolute;
    inset: 0;
    width: 100%;
    height: 100%;
  }
  .brand {
    position: absolute;
    left: 80px;
    top: 240px;
    display: flex;
    align-items: center;
    gap: 18px;
  }
  .brand__dot {
    width: 34px;
    height: 34px;
    border-radius: 50%;
    background: var(--honey);
  }
  .brand__name {
    font-family: "Almendra", serif;
    font-weight: 700;
    font-size: 66px;
    color: var(--ink);
    line-height: 1;
  }
  .title {
    position: absolute;
    right: 50px;
    top: 28px;
    margin: 0;
    font-family: "Rye", serif;
    font-weight: 400;
    text-align: right;
    line-height: 1.05;
    paint-order: stroke fill;
  }
  .title__top {
    display: block;
    font-size: 54px;
    color: var(--honey);
    -webkit-text-stroke: 4px var(--ink);
    margin-right: 70px;
  }
  .title__bottom {
    display: block;
    font-size: 50px;
    color: var(--ink);
    -webkit-text-stroke: 4px var(--honey);
  }
  .details {
    position: absolute;
    left: 665px;
    top: 318px;
    width: 330px;
    text-align: center;
    font-family: "Almendra", serif;
    font-weight: 700;
    color: var(--paper);
    font-size: 22px;
    line-height: 1.35;
  }
  .details p { margin: 0; }
  .details__phone {
    margin: 12px 0 8px !important;
    display: flex;
    justify-content: center;
    align-items: center;
    gap: 12px;
    font-family: "Roboto", sans-serif;
    font-size: 27px;
    color: var(--honey);
    letter-spacing: 0.5px;
  }
  .details__phone svg { width: 32px; height: 28px; }
</style>
</head>
<body>
  <section class="label">
    <svg class="label__wave" viewBox="0 0 1000 560" preserveAspectRatio="none" aria-hidden="true">
      <defs>
        <linearGradient id="graphiteFade" x1="0" y1="1" x2="1" y2="0">
          <stop offset="0" stop-color="#6f6b57"/>
          <stop offset="1" stop-color="#58585a"/>
        </linearGradient>
        <linearGradient id="honeyFade" x1="0" y1="0" x2="1" y2="0">
          <stop offset="0" stop-color="#ece62e"/>
          <stop offset="0.45" stop-color="#a59d55" stop-opacity="0.9"/>
          <stop offset="1" stop-color="#6f6b57" stop-opacity="0"/>
        </linearGradient>
      </defs>
      <path class="wave__band" d="M1000 170 C 800 170 700 220 640 310 C 560 440 400 490 130 500 L 130 560 L 1000 560 Z" fill="url(#graphiteFade)"/>
      <path class="wave__honey" d="M130 560 L130 522 C 400 518 560 490 680 405 L 1000 405 L 1000 560 Z" fill="url(#honeyFade)"/>
      <path class="wave__line" d="M860 182 C 740 195 672 245 626 312 C 546 436 390 484 130 490" fill="none" stroke="var(--honey)" stroke-width="3"/>
      <path class="wave__gap" d="M130 514 C 400 510 560 482 670 400" fill="none" stroke="var(--paper)" stroke-width="5"/>
    </svg>

    <div class="brand">
      <span class="brand__dot"></span>
      <span class="brand__name">Gentle Hive</span>
    </div>

    <h1 class="title">
      <span class="title__top">GOURMET</span>
      <span class="title__bottom">CANDIED PECANS</span>
    </h1>

    <div class="details">
      <p>Made with Cinnamon</p>
      <p>Brown Sugar &amp; Salt Order More</p>
      <p class="details__phone">
        <svg viewBox="0 0 34 30" aria-hidden="true">
          <polygon points="8,1 26,1 33,15 26,29 8,29 1,15" fill="var(--honey)"/>
          <path d="M11 9c2-2 4-2 5 0l1 2-2 2c1 2 3 4 5 5l2-2 2 1c2 1 2 3 0 5-3 2-7 0-10-3s-5-7-3-10z" fill="var(--graphite)"/>
        </svg>
        (555)014-2290
      </p>
      <p>Gentle Hive Market, LLC</p>
    </div>
  </section>
</body>
</html>
```